Web Site Design for a Finance (lending) Company

We are opening a new subsidiary that focuses on lending money in the real estate industry. We need a web site designed to represent the business.

The business is lending money to real estate investors. A typical client/borrower will be looking to borrow money to buy a house, renovate it and then sell it at a profit, all within 12 months or less.

Company name is RTV Finance. Our logo is attached.

Attached is a general outline for the web site. We're working on writing more text for each page but this should give you enough to get started with some ideas.

Competitor web site that I like a lot (as an example): https://dorvaleqcapital.example/. Many of the general items on this site match what we will need (description of loan programs, FAQ)

Target Market(s)

Real estate investors (generally individuals or small companies with just a few people) who are buying homes, renovating them and then selling them at a profit.

Industry/Entity Type

Finance

Coding

Coded - Design and coding required

Number of Pages Required

5+ page

Colors

Designer to choose colors to be used in the design.

Requirements
Must have
• Minimalist design. Clean lines without too much clutter. Some stock photography is ok but the photos should not be distracting. They should almost fade in to the background so that user can focus on the key information about what our company does instead. We are a finance company, not a design company, so the information about our products will be more interesting to site visitors than the art.
• Some minimalist examples from Snapboard:
• https://www.snapboardia.example/explore/minimalist-web-design/
Nice to have
• If you search in zoovle for "hard money lenders" you will find many examples of web sites from our competition. I have provided a link above to competitor web site that I like a lot.
• I have attached our logo in EPS format. Logo is green. Web site doesn't have to be green but it should be of a color that will work well with the logo.

```html
<!DOCTYPE html>
<html lang="en">
<head>
<meta charset="utf-8">
<title>RTV Finance</title>
<link href="https://fonts.googleapis.com/css2?family=Open+Sans:wght@400;600;700&display=swap" rel="stylesheet">
<style>
:root{
  --green:#0d4a2e;
  --green-dark:#073a23;
  --text:#5b5b5b;
  --muted:#8a8a8a;
  --btn:#a4a4ad;
  --band:#efefef;
  --footer:#2d2d2d;
  --footer-text:#cfcfcf;
  --orange:#f49a1a;
  --white:#ffffff;
}
*{box-sizing:border-box;margin:0;padding:0}
html,body{width:1200px;height:2586px;overflow:hidden}
body{font-family:"Open Sans",Arial,sans-serif;color:var(--text);background:var(--white);position:relative}
.wrap{width:1052px;margin:0 auto;position:relative}

/* header */
.site-header{height:122px}
.site-header .wrap{display:flex;justify-content:space-between;align-items:center;height:122px}
.brand{display:flex;align-items:center;gap:12px;font-size:30px;font-weight:700;color:var(--green)}
.brand-square{width:22px;height:22px;background:var(--green)}
.main-nav{display:flex;gap:8px;align-items:center}
.main-nav a{font-size:13px;font-weight:600;color:#222;text-decoration:none;padding:9px 12px;border-radius:20px}
.main-nav a.active{background:var(--green);color:var(--white);padding:9px 22px}

/* hero */
.hero{height:497px;position:relative;background:linear-gradient(120deg,#8a8580 0%,#4d4b4c 35%,#3b3a3c 60%,#7a6f68 100%);display:flex;flex-direction:column;align-items:center;justify-content:center;text-align:center;color:var(--white)}
.hero h1{font-size:36px;font-weight:700;letter-spacing:.5px;margin-bottom:14px;margin-top:-40px}
.hero p{font-size:23px;line-height:1.35;font-weight:400}
.hero-dots{position:absolute;bottom:34px;left:50%;transform:translateX(-50%);display:flex;gap:10px}
.hero-dots span{width:10px;height:10px;border-radius:50%;background:var(--white)}
.hero-dots span.on{background:var(--green)}

/* about */
.about{height:372px}
.about .wrap{display:flex;justify-content:space-between;padding-top:39px}
.about-copy{width:600px}
.section-heading{font-size:25px;font-weight:700;color:var(--green);line-height:1.3;letter-spacing:.5px;text-transform:uppercase}
.about-copy .section-heading{margin-bottom:26px;margin-top:8px}
.ticks{list-style:none}
.ticks li{display:flex;gap:22px;font-size:13.5px;line-height:1.7;margin-bottom:14px}
.ticks svg{flex:0 0 18px;margin-top:3px}
.about-photo{width:421px;height:283px;background:linear-gradient(180deg,#9aa3a4 0%,#b7aea2 45%,#5e7d3c 100%)}

/* loans */
.loans{height:462px;background:var(--band)}
.center-title{text-align:center;padding-top:44px;margin-bottom:33px}
.loan-cards{display:flex;justify-content:space-between}
.loan-card{width:512px;height:289px;background:var(--white);padding:22px 28px}
.loan-head{display:flex;align-items:center;gap:18px;margin-bottom:20px}
.loan-icon{width:56px;height:56px;border-radius:50%;background:var(--green);display:flex;align-items:center;justify-content:center}
.loan-head h3{font-size:16.5px;font-weight:700;color:var(--green);letter-spacing:.3px}
.body-text{font-size:13.5px;line-height:1.75;color:var(--text)}
.btn{display:inline-block;background:var(--btn);color:var(--white);font-size:12.5px;font-weight:700;text-transform:uppercase;width:160px;height:41px;line-height:41px;text-align:center;text-decoration:none;letter-spacing:.3px}
.loan-card .btn{margin-top:26px}

/* resources */
.resources{height:607px}
.resource-grid{display:flex;justify-content:space-between}
.resource{width:331px}
.resource-photo{height:203px;margin-bottom:18px}
.photo-coins{background:linear-gradient(180deg,#c9dce6 0%,#e9e2cf 55%,#b48a4e 100%)}
.photo-desk{background:linear-gradient(135deg,#c9a175 0%,#d8b48a 50%,#b38656 100%)}
.photo-plan{background:linear-gradient(135deg,#e6e9ec 0%,#cfd6dc 55%,#b84a3a 100%)}
.resource h3{font-size:17px;font-weight:700;color:var(--green);line-height:1.4;text-transform:uppercase;margin-bottom:6px}
.resource .btn{margin-top:22px}

/* membership */
.membership{height:242px;background:linear-gradient(180deg,#efefef 0%,#fafafa 100%)}
.membership .center-title{padding-top:50px;margin-bottom:36px}
.members{display:flex;justify-content:space-between;align-items:center;padding:0 10px}
.member{display:flex;align-items:center;gap:8px;font-size:30px;font-weight:700;color:#333}
.member-dot{width:24px;height:24px;border-radius:50%;background:var(--orange)}
.member-square{width:24px;height:24px;background:#3d7fd1}

/* footer */
.site-footer{height:284px;background:var(--footer);color:var(--footer-text)}
.site-footer .wrap{display:flex;padding-top:38px}
.footer-brand{width:310px}
.footer-brand .brand{color:#bdbdbd;margin:10px 0 20px}
.footer-brand .brand-square{background:#bdbdbd}
.copyright{font-size:12.5px;line-height:1.7}
.footer-col h4{font-size:13.5px;font-weight:700;color:var(--white);margin-bottom:14px;letter-spacing:.3px}
.sitemap{width:209px}
.sitemap a{display:block;color:var(--footer-text);font-size:12.5px;text-decoration:none;margin-bottom:12px}
.contact{width:290px}
.contact p{font-size:12.5px;line-height:1.7;margin-bottom:12px;display:flex;gap:18px;align-items:center}
.contact p.addr{display:block}
.newsletter{width:243px}
.subscribe{display:flex;height:42px;margin-bottom:22px}
.subscribe span{flex:1;background:var(--white);color:#444;font-size:12px;line-height:42px;padding-left:12px}
.subscribe b{width:42px;background:var(--green-dark);display:flex;align-items:center;justify-content:center}
.social{display:flex;gap:20px;margin-top:4px}
.social span{width:18px;height:18px;border-radius:50%;background:var(--white)}
.chat-box{position:absolute;right:79px;bottom:0;width:219px;height:48px;background:var(--orange);color:var(--white);font-size:16px;font-weight:700;display:flex;align-items:center;justify-content:center;gap:10px;letter-spacing:.5px}
</style>
</head>
<body>

<header class="site-header">
  <div class="wrap">
    <div class="brand"><span class="brand-square"></span>RTV Finance</div>
    <nav class="main-nav">
      <a href="#" class="active">HOME</a>
      <a href="#">ABOUT US</a>
      <a href="#">LOANS</a>
      <a href="#">RESOURCES</a>
      <a href="#">CONTACT US</a>
    </nav>
  </div>
</header>

<section class="hero" role="img" aria-label="Photo of a loan advisor reviewing documents with a couple at a desk">
  <h1>WELCOME TO RTV FINANCE</h1>
  <p>We are a new subsidiary company that focuses on lending money<br>in the real estate industry.</p>
  <div class="hero-dots"><span class="on"></span><span></span><span></span><span></span></div>
</section>

<section class="about">
  <div class="wrap">
    <div class="about-copy">
      <h2 class="section-heading">Local real estate experts lending to<br>local real estate investors</h2>
      <ul class="ticks">
        <li><svg width="18" height="18" viewBox="0 0 18 18"><circle cx="9" cy="9" r="7.5" fill="none" stroke="#0d4a2e" stroke-width="2"/><path d="M5.5 9.2l2.4 2.4 4.6-4.8" fill="none" stroke="#0d4a2e" stroke-width="2"/></svg><span>RTV Finance is a local business with local knowledge and strong industry relationships. A partner with a wide network who offers value added services.</span></li>
        <li><svg width="18" height="18" viewBox="0 0 18 18"><circle cx="9" cy="9" r="7.5" fill="none" stroke="#0d4a2e" stroke-width="2"/><path d="M5.5 9.2l2.4 2.4 4.6-4.8" fill="none" stroke="#0d4a2e" stroke-width="2"/></svg><span>RTV has an established pool of experienced investors available for your real</span></li>
        <li><svg width="18" height="18" viewBox="0 0 18 18"><circle cx="9" cy="9" r="7.5" fill="none" stroke="#0d4a2e" stroke-width="2"/><path d="M5.5 9.2l2.4 2.4 4.6-4.8" fill="none" stroke="#0d4a2e" stroke-width="2"/></svg><span>Loans offered (Fix and Flip, Commercial).</span></li>
        <li><svg width="18" height="18" viewBox="0 0 18 18"><circle cx="9" cy="9" r="7.5" fill="none" stroke="#0d4a2e" stroke-width="2"/><path d="M5.5 9.2l2.4 2.4 4.6-4.8" fill="none" stroke="#0d4a2e" stroke-width="2"/></svg><span>Why borrow from RTV (experts, fast approval, professional, a partner, selective, competitive rates and fees).</span></li>
      </ul>
    </div>
    <div class="about-photo" role="img" aria-label="Photo of a family looking at a brick house on a green lawn"></div>
  </div>
</section>

<section class="loans">
  <div class="wrap">
    <h2 class="section-heading center-title">Loans</h2>
    <div class="loan-cards">
      <article class="loan-card">
        <div class="loan-head">
          <div class="loan-icon"><svg width="22" height="26" viewBox="0 0 22 26"><path d="M2 1h12l6 6v18H2z" fill="#fff"/><path d="M6 12h10M6 16h10M6 20h7" stroke="#0d4a2e" stroke-width="2"/></svg></div>
          <h3>FIX AND FLIP LOANS</h3>
        </div>
        <p class="body-text">Aliquam molestie, mi et imperdiet euismod, dui purus auctor tellus, et interdum lacus lectus et ante. Sed accumsan sollicitudin sapien, sit amet adipiscing turpis gravida ac. In congue, neque ac lobortis volutpat, libero mauris varius mi, vitae suscipit ipsum<br>ligula vitae risus.</p>
        <a href="#" class="btn">Read more</a>
      </article>
      <article class="loan-card">
        <div class="loan-head">
          <div class="loan-icon"><svg width="20" height="26" viewBox="0 0 20 26"><rect x="2" y="1" width="16" height="24" fill="#fff"/><path d="M6 6h3M11 6h3M6 11h3M11 11h3M6 16h3M11 16h3M8 21h4v4H8z" stroke="#0d4a2e" stroke-width="2"/></svg></div>
          <h3>COMMERCIAL HARD MONEY LOANS</h3>
        </div>
        <p class="body-text">Aliquam molestie, mi et imperdiet euismod, dui purus auctor tellus, et interdum lacus lectus et ante. Sed accumsan sollicitudin sapien, sit amet adipiscing turpis gravida ac. In congue, neque ac lobortis volutpat, libero mauris varius mi, vitae suscipit ipsum<br>ligula vitae risus.</p>
        <a href="#" class="btn">Read more</a>
      </article>
    </div>
  </div>
</section>

<section class="resources">
  <div class="wrap">
    <h2 class="section-heading center-title">Resources</h2>
    <div class="resource-grid">
      <article class="resource">
        <div class="resource-photo photo-coins" role="img" aria-label="Photo of a hand placing a coin on coin stacks before a city skyline"></div>
        <h3>Nam fermentum vestibulum purus id aliquet</h3>
        <p class="body-text">Aliquam molestie, mi et imperdiet euismod, dui purus auctor tellus, et interdum lacus lectus et ante. Sed accumsan sollicitudin sapien, sit amet adipiscing turpis gravida ac.</p>
        <a href="#" class="btn">Read more</a>
      </article>
      <article class="resource">
        <div class="resource-photo photo-desk" role="img" aria-label="Photo of a magnifying glass over a house sketch on a wooden table"></div>
        <h3>Nam fermentum vestibulum purus id aliquet</h3>
        <p class="body-text">Aliquam molestie, mi et imperdiet euismod, dui purus auctor tellus, et interdum lacus lectus et ante. Sed accumsan sollicitudin sapien, sit amet adipiscing turpis gravida ac.</p>
        <a href="#" class="btn">Read more</a>
      </article>
      <article class="resource">
        <div class="resource-photo photo-plan" role="img" aria-label="Photo of house keys and a small model house on building plans"></div>
        <h3>Nam fermentum vestibulum purus id aliquet</h3>
        <p class="body-text">Aliquam molestie, mi et imperdiet euismod, dui purus auctor tellus, et interdum lacus lectus et ante. Sed accumsan sollicitudin sapien, sit amet adipiscing turpis gravida ac.</p>
        <a href="#" class="btn">Read more</a>
      </article>
    </div>
  </div>
</section>

<section class="membership">
  <div class="wrap">
    <h2 class="section-heading center-title">Industry Membership</h2>
    <div class="members">
      <div class="member"><span class="member-dot"></span>Pennway</div>
      <div class="member"><span class="member-dot"></span>Brightly</div>
      <div class="member">Crownfield</div>
      <div class="member"><span class="member-dot"></span>Tandem</div>
      <div class="member"><span class="member-square"></span>Steadmark</div>
    </div>
  </div>
</section>

<footer class="site-footer">
  <div class="wrap">
    <div class="footer-brand">
      <div class="brand"><span class="brand-square"></span>RTV Finance</div>
      <p class="copyright">Copyright © 2017. Company Name.<br>All Right Reserved</p>
    </div>
    <div class="footer-col sitemap">
      <h4>SITE MAP</h4>
      <a href="#">Home</a><a href="#">About us</a><a href="#">Loans</a><a href="#">Resources</a><a href="#">Contact us</a>
    </div>
    <div class="footer-col contact">
      <h4>CONTACT ADDRESS</h4>
      <p class="addr">4172 Larkspur Lane,<br>Brookvale, BV2 7QT</p>
      <p><svg width="12" height="12" viewBox="0 0 12 12"><path d="M2 1l2.5 0 1 3-1.5 1a7 7 0 0 0 3 3l1-1.5 3 1V11C5 11 1 7 1 2z" fill="#cfcfcf"/></svg>1-800-555-0142</p>
      <p><svg width="13" height="10" viewBox="0 0 13 10"><rect width="13" height="10" fill="#cfcfcf"/><path d="M0 0l6.5 5L13 0" fill="none" stroke="#2d2d2d" stroke-width="1.2"/></svg>info@rtvfinance.example</p>
    </div>
    <div class="footer-col newsletter">
      <h4>EMAIL NEWSLETTER</h4>
      <div class="subscribe"><span>Enter Email Address</span><b><svg width="16" height="16" viewBox="0 0 16 16"><path d="M1 8l14-7-4 14-3-5z" fill="#fff"/></svg></b></div>
      <h4>FOLLOW US</h4>
      <div class="social" aria-label="Social links"><span></span><span></span><span></span><span></span><span></span></div>
    </div>
  </div>
  <div class="chat-box"><svg width="18" height="14" viewBox="0 0 18 14"><path d="M1 1h11v8H5l-3 3V9H1z" fill="#fff"/><path d="M13 4h4v7h-1v2l-2-2H8v-1h5z" fill="#fff"/></svg>CHAT BOX<svg width="10" height="14" viewBox="0 0 10 14"><path d="M2 1l6 6-6 6" fill="none" stroke="#fff" stroke-width="2.4"/></svg></div>
</footer>

</body>
</html>
```